Web Design Project and logo

We need a new web design and logo for www.kz7ventures.com

It is a mobile app development company. Site needs to look very cool/trendy as does the new logo.

Looking for the design (uncoded) and the logo file that my developers can then use to build out the site.

An example of a nice competitor site is www.thecodegarage.com

We want something that looks fresh, clean and hip.

Also development of business cards.

Target Market(s)

Small to mid sized companies

Industry/Entity Type

Business

Requirements
Must have
• Ability to request a quote
Should look very trendy like www.thecodegarage.com as an example of a competitor site

```html
<!DOCTYPE html>
<html lang="en">
<head>
<meta charset="utf-8">
<title>KZ7 Ventures – Home page layouts</title>
<link rel="stylesheet" href="https://fonts.googleapis.com/css2?family=Open+Sans:wght@300;400;600;700&display=swap">
<style>
:root{
  --stage:#8a8a8a;
  --red:#f04a32;
  --ink:#333;
  --muted:#8a8a8a;
  --soft:#f4f4f4;
  --line:#e2e2e2;
  --white:#fff;
  --dark:#111;
  --hero-a:#1a0d0a;
  --hero-b:#6a1e12;
  --hero-c:#c0492a;
  --slide-dark:#1b1615;
  --slide-mid:#2c2422;
}
*{box-sizing:border-box;margin:0;padding:0}
html,body{width:1200px;height:1000px;overflow:hidden}
body{background:var(--stage);font-family:'Open Sans',Arial,sans-serif;color:var(--ink);position:relative}
.page{position:absolute;top:10px;width:416px;height:948px;background:var(--white);box-shadow:0 2px 10px rgba(0,0,0,.35);overflow:hidden}
.page--home{left:164px}
.page--promo{left:620px}
.abs{position:absolute}

/* nav */
.nav{top:0;left:0;width:416px;height:24px;background:var(--white);display:flex;align-items:center;font-size:4.5px;color:var(--muted);text-transform:uppercase}
.brand{position:absolute;left:10px;top:3px;font-size:13px;font-weight:700;color:var(--red);letter-spacing:-.5px;line-height:18px}
.nav-links{position:absolute;left:82px;display:flex;gap:10px}
.nav-links .is-active{color:var(--ink);font-weight:600}
.nav-call{position:absolute;left:250px}
.nav-lang{position:absolute;left:318px}
.nav-cta{position:absolute;right:6px;top:6px;padding:3px 6px;border:1px solid #ccc;border-radius:2px;background:#eee}

/* hero */
.hero{top:24px;left:0;width:416px;height:241px;overflow:hidden}
.hero-photo{position:absolute;inset:0}
.page--home .hero-photo{background:radial-gradient(ellipse at 40% 45%,var(--hero-c) 0%,var(--hero-b) 30%,var(--hero-a) 70%),var(--hero-a)}
.page--promo .hero-photo{background:radial-gradient(ellipse at 75% 30%,#4a2a22 0%,var(--slide-dark) 60%,#0c0a0a 100%)}
.promo-device{position:absolute;left:0;top:0;width:160px;height:200px;background:linear-gradient(180deg,var(--slide-mid),var(--slide-dark))}
.promo-mark{position:absolute;left:198px;top:46px;width:150px;height:26px;background:linear-gradient(#f3b54a,#d7892a);border-radius:3px}
.hero-title{position:absolute;left:0;width:416px;top:72px;text-align:center;color:var(--white);font-size:16px;font-weight:300}
.hero-sub{position:absolute;left:74px;top:93px;width:268px;background:rgba(0,0,0,.75);color:#ddd;font-size:4.5px;text-align:center;padding:2px 0}
.hero-actions{position:absolute;top:116px;left:0;width:416px;display:flex;justify-content:center;gap:10px}
.btn{background:var(--red);color:var(--white);font-size:4.8px;text-transform:uppercase;padding:6px 7px;border-radius:1px;font-weight:600}
.promo-copy{position:absolute;left:165px;top:92px;width:230px;text-align:center;color:var(--white);font-size:10.5px;font-weight:300;line-height:14px}
.promo-action{position:absolute;left:240px;top:150px}
.features{position:absolute;top:201px;left:4px;display:flex;gap:6px}
.feature{width:132px;height:36px;background:rgba(0,0,0,.7);display:flex;gap:6px;padding:5px;color:#eee}
.feature svg{flex:none}
.feature h4{font-size:4.6px;font-weight:600;text-transform:uppercase;margin-bottom:1px}
.feature p{font-size:4px;line-height:5px;color:#ccc}

/* section titles */
.section-title{text-align:center;font-size:8px;font-weight:300;text-transform:uppercase;line-height:9px;color:var(--ink)}
.section-title em{font-style:normal;color:var(--red);display:block}
.experiences-head{top:265px;left:0;width:416px;height:43px;background:var(--soft);padding-top:11px}

/* steps */
.steps{top:308px;left:0;width:416px;height:119px;background:var(--soft);display:flex}
.step{width:83.2px;border-right:1px solid var(--line);padding:20px 6px 0;text-align:center;position:relative}
.step h5{font-size:4.6px;font-weight:400;text-transform:uppercase;margin:6px 8px 8px;line-height:6px;min-height:12px}
.step p{font-size:4.2px;line-height:5.6px;text-align:left;color:var(--muted)}
.step .more{position:absolute;left:6px;bottom:12px;font-size:4px;color:var(--muted)}
.step--active{background:var(--red);color:var(--white)}
.step--active p,.step--active .more{color:var(--white)}
.step--active::before{content:"";position:absolute;left:36px;top:0;border:5px solid transparent;border-top-color:var(--soft)}

/* about */
.about{top:457px;left:11px;width:130px}
.block-title{font-size:8px;font-weight:300;text-transform:uppercase;margin-bottom:2px;color:var(--ink)}
.about p,.testimonial p{font-size:4.2px;line-height:6px;color:var(--muted)}
.read-more{font-size:4px;color:var(--muted);margin-top:10px}
.video{top:460px;left:154px;width:123px;height:70px;background:linear-gradient(120deg,#2b3b4d 0%,#1786c9 55%,#5bc2f0 100%)}
.play{position:absolute;left:48px;top:22px}
.testimonial{top:457px;left:300px;width:110px}
.avatars{display:flex;gap:10px;margin:3px 0 10px}
.avatar{width:28px;height:28px;background:#9d9d9d}
.avatar--active{background:var(--red)}

/* facts */
.facts{top:565px;left:0;width:416px;height:230px;background:var(--soft)}
.facts-head{position:absolute;top:12px;left:0;width:416px}
.facts-head .section-title{font-size:7.5px}
.facts-head em{font-weight:600;font-size:6.8px}
.phone-shot{top:52px;left:44px;width:87px;height:172px;background:linear-gradient(#1a1a1a,#2d2d2d);border-radius:12px}
.phone-screen{position:absolute;left:7px;top:26px;width:73px;height:110px;background:linear-gradient(135deg,#2e8a5a,#bb4a2a 40%,#2a5fa8 70%,#e6e6e6)}
.laptop{top:70px;left:262px;width:160px;height:147px;background:linear-gradient(#0b0b0b,#151515 85%,#cfcfcf 86%,#9d9d9d)}
.laptop-screen{position:absolute;left:8px;top:8px;width:150px;height:115px;background:linear-gradient(160deg,#1e2224,#121416)}
.equation{top:60px;left:150px;width:112px;text-align:center;font-size:8px;line-height:8px;text-transform:uppercase;font-weight:300}
.equation b{font-weight:700;display:block}
.equation .op{color:#bbb;font-size:10px;line-height:13px;margin:10px 0}
.equation .hi{color:var(--red)}

/* tech strip */
.tech{top:805px;left:0;width:416px;height:45px;display:flex;align-items:center;justify-content:center;gap:14px}
.tech-badge{width:42px;height:10px;background:#d4d4d4;border-radius:2px}
.arrow{color:#999;font-size:9px}

/* footer */
.footer{top:852px;left:0;width:416px;height:81px;background:var(--soft);font-size:4.2px;color:var(--muted)}
.footer .brand{left:11px;top:12px}
.footer-about{position:absolute;left:11px;top:36px;width:105px;line-height:5.8px}
.footer h6{font-size:4.4px;font-weight:400;text-transform:uppercase;margin-bottom:6px}
.footer ul{list-style:none;line-height:7.6px;text-transform:uppercase}
.footer-menu{position:absolute;left:135px;top:14px}
.footer-menu li:first-child{color:var(--ink)}
.footer-contact{position:absolute;left:190px;top:14px;width:100px}
.footer-contact li{display:flex;gap:5px;line-height:5.6px;margin-bottom:3px}
.footer-follow{position:absolute;left:310px;top:14px;width:100px}
.socials{display:flex;gap:5px;margin-bottom:8px}
.social{width:6px;height:6px;border-radius:50%;background:#9a9a9a}
.newsletter{display:flex;margin-top:4px}
.newsletter span{flex:1;background:var(--white);border:1px solid var(--line);padding:2px 4px;font-size:3.8px}
.newsletter i{width:12px;background:var(--white);border:1px solid var(--line);border-left:0}
.copyright{top:933px;left:0;width:416px;height:15px;background:var(--dark);color:#ddd;font-size:3.8px;text-align:center;line-height:15px;text-transform:uppercase}
</style>
</head>
<body>

<!-- Home page -->
<section class="page page--home">
  <header class="abs nav">
    <span class="brand">KZ7</span>
    <nav class="nav-links"><span class="is-active">Home</span><span>Our services</span><span>Latest news</span><span>Contact</span></nav>
    <span class="nav-call">Call us on: +00 000 0000</span>
    <span class="nav-lang">English ▾</span>
    <span class="nav-cta">I need app now!</span>
  </header>
  <div class="abs hero">
    <div class="hero-photo" role="img" aria-label="Close-up photo of a fingertip touching a glowing screen"></div>
    <h1 class="hero-title">THE NO1 APPS</h1>
    <p class="hero-sub">KZ7 Ventures helps you to a specialty mobile solutions provider with expertise across all the major mobile platforms.</p>
    <div class="hero-actions"><span class="btn">See the details now</span><span class="btn">I need app now</span></div>
    <div class="features">
      <div class="feature"><svg width="14" height="14" viewBox="0 0 14 14"><rect x="1" y="2" width="7" height="10" rx="1" fill="none" stroke="#fff"/><rect x="9" y="5" width="4" height="7" rx="1" fill="none" stroke="#fff"/></svg><div><h4>Mobile services</h4><p>Our comprehensive range of consulting services takes you from idea through development.</p></div></div>
      <div class="feature"><svg width="14" height="14" viewBox="0 0 14 14"><path d="M7 12 1.5 6.5a3 3 0 0 1 5.5-3 3 3 0 0 1 5.5 3z" fill="#fff"/></svg><div><h4>Quality through experience</h4><p>Our team of engineers know what it takes to serve more than 1,000,000 happy customers.</p></div></div>
      <div class="feature"><svg width="14" height="14" viewBox="0 0 14 14"><circle cx="7" cy="7" r="5" fill="none" stroke="#fff"/><path d="M7 1v12M1 7h12" stroke="#fff"/></svg><div><h4>I want you!</h4><p>KZ7 is always looking for talented developers. If you have what it takes, do not hesitate to contact us!</p></div></div>
    </div>
  </div>
  <div class="abs experiences-head"><h2 class="section-title">Unique experiences for<em>mobile</em></h2></div>
  <div class="abs steps">
    <div class="step step--active"><svg width="12" height="14" viewBox="0 0 12 14"><path d="M6 1C4 5 1.5 7 1.5 9.5a4.5 4.5 0 0 0 9 0C10.5 7 8 5 6 1z" fill="#fff"/></svg><h5>Needs</h5><p>Lorem Ipsum is simply dummy text of the printing and typesetting industry.</p><span class="more">Read more</span></div>
    <div class="step"><svg width="12" height="14" viewBox="0 0 12 14"><path d="M6 1c3 2 3 7 2 9H4C3 8 3 3 6 1zM4 10l-2 3h3zM8 10l2 3H7z" fill="#4a5560"/></svg><h5>Planning and rapid prototyping</h5><p>Lorem Ipsum is simply dummy text of the printing and typesetting industry.</p><span class="more">Read more</span></div>
    <div class="step"><svg width="12" height="14" viewBox="0 0 12 14"><rect x="2" y="1" width="8" height="12" rx="1.5" fill="none" stroke="#4a5560" stroke-width="1.4"/><rect x="4" y="4" width="4" height="5" fill="#4a5560"/></svg><h5>Coding and testing</h5><p>Lorem Ipsum is simply dummy text of the printing and typesetting industry.</p><span class="more">Read more</span></div>
    <div class="step"><svg width="16" height="14" viewBox="0 0 16 14"><path d="M4 12a3 3 0 0 1 0-6 4 4 0 0 1 8 0 3 3 0 0 1 0 6z" fill="#4a5560"/></svg><h5>Completion and market introduction</h5><p>Lorem Ipsum is simply dummy text of the printing and typesetting industry.</p><span class="more">Read more</span></div>
    <div class="step"><svg width="14" height="14" viewBox="0 0 14 14"><path d="M2 12h2V8H2zM5 12h2V6H5zM8 12h2V4H8zM11 12h2V2h-2z" fill="#4a5560"/></svg><h5>Analysis &amp; improvements</h5><p>Lorem Ipsum is simply dummy text of the printing and typesetting industry.</p><span class="more">Read more</span></div>
  </div>
  <div class="abs about"><h3 class="block-title">About us</h3><p>KZ7 Ventures is a specialty mobile solutions provider with expertise across all the major mobile platforms. We have a track record with several apps reaching the top 10 most downloaded lists. Deep knowledge of how to create and manage robust and intuitive apps has been acquired by the experience rendered from serving 1,000,000 customers.</p><p class="read-more">Read more</p></div>
  <div class="abs video" role="img" aria-label="Video still of a businessman holding a smartphone with a digital network backdrop"><svg class="play" width="26" height="26" viewBox="0 0 26 26"><circle cx="13" cy="13" r="12" fill="none" stroke="#fff" stroke-width="2"/><path d="M10 7.5v11l9-5.5z" fill="#fff"/></svg></div>
  <div class="abs testimonial"><h3 class="block-title">Customers are saying</h3><div class="avatars"><span class="avatar avatar--active"></span><span class="avatar"></span><span class="avatar"></span></div><p>Lorem Ipsum is simply dummy text of the printing and typesetting industry.</p><p class="read-more">Read more</p></div>
  <div class="abs facts">
    <div class="facts-head"><h2 class="section-title">A fact worth a thousand words,<em>our clients love us and why they keep coming back</em></h2></div>
    <div class="abs phone-shot" role="img" aria-label="Smartphone showing a colourful word game board"><div class="phone-screen"></div></div>
    <div class="abs equation"><b>1,000,000</b>Happy customers<div class="op">+</div><b>X years</b>Off experience<div class="op">+</div><b>Famous</b>Applications<div class="op">=</div><b class="hi">100%</b>Satisfaction</div>
    <div class="abs laptop" role="img" aria-label="Laptop showing a code editor"><div class="laptop-screen"></div></div>
  </div>
  <div class="abs tech"><span class="arrow">‹</span><span class="tech-badge"></span><span class="tech-badge"></span><span class="tech-badge"></span><span class="tech-badge"></span><span class="tech-badge"></span><span class="tech-badge"></span><span class="arrow">›</span></div>
  <footer class="abs footer">
    <span class="brand">KZ7</span>
    <p class="footer-about">KZ7 Ventures is a specialty mobile solutions provider with expertise across all the major mobile platforms.</p>
    <div class="footer-menu"><h6>Menu</h6><ul><li>Home</li><li>Our services</li><li>Latest news</li><li>Contact</li></ul></div>
    <div class="footer-contact"><h6>Contact us</h6><ul><li><span>◉</span><span>Address: Unit 4 Harbour Yard, Linden Street, Eastfield EF3 9QT</span></li><li><span>✆</span><span>Phone: +00 0000 000</span></li><li><span>✉</span><span>Email: mail@example.com</span></li></ul></div>
    <div class="footer-follow"><h6>Follow us</h6><div class="socials"><span class="social"></span><span class="social"></span><span class="social"></span><span class="social"></span></div><h6>Sign up for our newsletter:</h6><div class="newsletter"><span>Enter your email adress here...</span><i></i></div></div>
  </footer>
  <div class="abs copyright">Copyright KZ7 Ventures 2013. All rights reserved.</div>
</section>

<!-- Promo page -->
<section class="page page--promo">
  <header class="abs nav">
    <span class="brand">KZ7</span>
    <nav class="nav-links"><span class="is-active">Home</span><span>Our services</span><span>Latest news</span><span>Contact</span></nav>
    <span class="nav-call">Call us on: +00 000 0000</span>
    <span class="nav-lang">English ▾</span>
    <span class="nav-cta">I need app now!</span>
  </header>
  <div class="abs hero">
    <div class="hero-photo" role="img" aria-label="Dark blurred background"></div>
    <div class="promo-device" role="img" aria-label="Photo of a hand holding a smartphone running the Wordspree word game"></div>
    <div class="promo-mark" role="img" aria-label="Wordspree game title set on letter tiles"></div>
    <p class="promo-copy">MORE THAN 1,000,000 DOWNLOADS!<br>TOP 10 FOR SEVERAL MONTHS!</p>
    <span class="btn promo-action">See the details now</span>
    <div class="features">
      <div class="feature"><svg width="14" height="14" viewBox="0 0 14 14"><rect x="1" y="2" width="7" height="10" rx="1" fill="none" stroke="#fff"/><rect x="9" y="5" width="4" height="7" rx="1" fill="none" stroke="#fff"/></svg><div><h4>Mobile services</h4><p>Our comprehensive range of consulting services takes you from idea through development.</p></div></div>
      <div class="feature"><svg width="14" height="14" viewBox="0 0 14 14"><path d="M7 12 1.5 6.5a3 3 0 0 1 5.5-3 3 3 0 0 1 5.5 3z" fill="#fff"/></svg><div><h4>Quality through experience</h4><p>Our team of engineers know what it takes to serve more than 1,000,000 happy customers.</p></div></div>
      <div class="feature"><svg width="14" height="14" viewBox="0 0 14 14"><circle cx="7" cy="7" r="5" fill="none" stroke="#fff"/><path d="M7 1v12M1 7h12" stroke="#fff"/></svg><div><h4>I want you!</h4><p>KZ7 is always looking for talented developers. If you have what it takes, do not hesitate to contact us!</p></div></div>
    </div>
  </div>
  <div class="abs experiences-head"><h2 class="section-title">Unique experiences for<em>mobile</em></h2></div>
  <div class="abs steps">
    <div class="step step--active"><svg width="12" height="14" viewBox="0 0 12 14"><path d="M6 1C4 5 1.5 7 1.5 9.5a4.5 4.5 0 0 0 9 0C10.5 7 8 5 6 1z" fill="#fff"/></svg><h5>Needs</h5><p>Lorem Ipsum is simply dummy text of the printing and typesetting industry.</p><span class="more">Read more</span></div>
    <div class="step"><svg width="12" height="14" viewBox="0 0 12 14"><path d="M6 1c3 2 3 7 2 9H4C3 8 3 3 6 1zM4 10l-2 3h3zM8 10l2 3H7z" fill="#4a5560"/></svg><h5>Planning and rapid prototyping</h5><p>Lorem Ipsum is simply dummy text of the printing and typesetting industry.</p><span class="more">Read more</span></div>
    <div class="step"><svg width="12" height="14" viewBox="0 0 12 14"><rect x="2" y="1" width="8" height="12" rx="1.5" fill="none" stroke="#4a5560" stroke-width="1.4"/><rect x="4" y="4" width="4" height="5" fill="#4a5560"/></svg><h5>Coding and testing</h5><p>Lorem Ipsum is simply dummy text of the printing and typesetting industry.</p><span class="more">Read more</span></div>
    <div class="step"><svg width="16" height="14" viewBox="0 0 16 14"><path d="M4 12a3 3 0 0 1 0-6 4 4 0 0 1 8 0 3 3 0 0 1 0 6z" fill="#4a5560"/></svg><h5>Completion and market introduction</h5><p>Lorem Ipsum is simply dummy text of the printing and typesetting industry.</p><span class="more">Read more</span></div>
    <div class="step"><svg width="14" height="14" viewBox="0 0 14 14"><path d="M2 12h2V8H2zM5 12h2V6H5zM8 12h2V4H8zM11 12h2V2h-2z" fill="#4a5560"/></svg><h5>Analysis &amp; improvements</h5><p>Lorem Ipsum is simply dummy text of the printing and typesetting industry.</p><span class="more">Read more</span></div>
  </div>
  <div class="abs about"><h3 class="block-title">About us</h3><p>KZ7 Ventures is a specialty mobile solutions provider with expertise across all the major mobile platforms. We have a track record with several apps reaching the top 10 most downloaded lists. Deep knowledge of how to create and manage robust and intuitive apps has been acquired by the experience rendered from serving 1,000,000 customers.</p><p class="read-more">Read more</p></div>
  <div class="abs video" role="img" aria-label="Video still of a businessman holding a smartphone with a digital network backdrop"><svg class="play" width="26" height="26" viewBox="0 0 26 26"><circle cx="13" cy="13" r="12" fill="none" stroke="#fff" stroke-width="2"/><path d="M10 7.5v11l9-5.5z" fill="#fff"/></svg></div>
  <div class="abs testimonial"><h3 class="block-title">Customers are saying</h3><div class="avatars"><span class="avatar avatar--active"></span><span class="avatar"></span><span class="avatar"></span></div><p>Lorem Ipsum is simply dummy text of the printing and typesetting industry.</p><p class="read-more">Read more</p></div>
  <div class="abs facts">
    <div class="facts-head"><h2 class="section-title">A fact worth a thousand words,<em>our clients love us and why they keep coming back</em></h2></div>
    <div class="abs phone-shot" role="img" aria-label="Smartphone showing a colourful word game board"><div class="phone-screen"></div></div>
    <div class="abs equation"><b>1,000,000</b>Happy customers<div class="op">+</div><b>X years</b>Off experience<div class="op">+</div><b>Famous</b>Applications<div class="op">=</div><b class="hi">100%</b>Satisfaction</div>
    <div class="abs laptop" role="img" aria-label="Laptop showing a code editor"><div class="laptop-screen"></div></div>
  </div>
  <div class="abs tech"><span class="arrow">‹</span><span class="tech-badge"></span><span class="tech-badge"></span><span class="tech-badge"></span><span class="tech-badge"></span><span class="tech-badge"></span><span class="tech-badge"></span><span class="arrow">›</span></div>
  <footer class="abs footer">
    <span class="brand">KZ7</span>
    <p class="footer-about">KZ7 Ventures is a specialty mobile solutions provider with expertise across all the major mobile platforms.</p>
    <div class="footer-menu"><h6>Menu</h6><ul><li>Home</li><li>Our services</li><li>Latest news</li><li>Contact</li></ul></div>
    <div class="footer-contact"><h6>Contact us</h6><ul><li><span>◉</span><span>Address: Unit 4 Harbour Yard, Linden Street, Eastfield EF3 9QT</span></li><li><span>✆</span><span>Phone: +00 0000 000</span></li><li><span>✉</span><span>Email: mail@example.com</span></li></ul></div>
    <div class="footer-follow"><h6>Follow us</h6><div class="socials"><span class="social"></span><span class="social"></span><span class="social"></span><span class="social"></span></div><h6>Sign up for our newsletter:</h6><div class="newsletter"><span>Enter your email adress here...</span><i></i></div></div>
  </footer>
  <div class="abs copyright">Copyright KZ7 Ventures 2013. All rights reserved.</div>
</section>

</body>
</html>
```